Summit Bodyform Gym Website

We need a website design for our gym.

Summit is the UAE's first calisthenics and parkour gym. The theme under which the gym revolves is that one does not require any machinery to workout as our bodies could be themselves the machinery. The gym is designed to be the more of a social hub rather than an "in-and-out" gym, where people come train, have fun, hang out and socialize for a few hours rather than just train for 60 minutes then leave. The gym is designed to be a big open space with lots of natural sunlight, natural wood and plants all over the place to create a natural and refreshing setting. We also use recycled material throughout the gym and recycle our waste as being green is part of our philosophy. We currently also have some of the world's top and most recognized calisthenics athletes working with us.

We would like our website to reflect all that as well as provide a simple, interactive and fun way for visitors to be able to get class and gym information, check out gym media and contact us for bookings.

Target Market(s)

Ages 15-35

Industry/Entity Type

Fitness

Coding

Coded - Design and coding required

Number of Pages Required

4 page

Font styles to use
Decorative

Colors
0792cd

Requirements
Must have
• Class descriptions
• Gym description
• Class schedules
• Trainer profiles
• Gym philosophy
• Contact Details
Nice to have
• A link to contact us directly for a free first trial class

```html
<!DOCTYPE html>
<html lang="en">
<head>
<meta charset="utf-8">
<title>Summit Gym</title>
<link rel="stylesheet" href="https://fonts.googleapis.com/css2?family=Lato:wght@400;700&family=Open+Sans:wght@400;600&family=Montserrat:wght@500&display=swap">
<style>
:root{
  --brand:#0b98c4;
  --brand-deep:#0a86ad;
  --ink:#333;
  --ink-soft:#555;
  --slate:#262d35;
  --night:#14191e;
  --white:#fff;
  --nav-bg:#fafafa;
}
*{box-sizing:border-box;margin:0;padding:0}
html,body{width:1200px;height:2406px;overflow:hidden;background:#fff}
body{font-family:"Lato",sans-serif;color:var(--ink);position:relative}
.page{position:relative;width:1200px;height:2406px;overflow:hidden}
section,header,footer{position:absolute;left:0;width:1200px}

/* header */
.site-header{top:0;height:91px;background:var(--nav-bg);border-top:4px solid var(--brand)}
.brand{position:absolute;left:112px;top:18px;display:flex;align-items:center;gap:10px}
.brand-dot{width:26px;height:26px;border-radius:50%;background:var(--brand)}
.brand-name{font-family:"Lato",sans-serif;font-weight:700;font-size:30px;color:#1e2a33}
.main-nav{position:absolute;left:302px;top:0;display:flex;height:62px}
.main-nav a{display:flex;align-items:center;font-size:13.5px;color:#222;text-decoration:none;padding:0 22px;height:62px}
.main-nav a.active{background:var(--brand);color:#fff;width:72px;justify-content:center;padding:0;position:relative}
.main-nav a.active::after{content:"";position:absolute;bottom:8px;left:50%;margin-left:-5px;border:5px solid transparent;border-bottom-color:#fff;border-top:0}

/* hero */
.hero{top:91px;height:408px;background:linear-gradient(180deg,#6e4a30 0%,#8a5e3c 35%,#3b3a38 70%,#5a2a24 100%)}
.hero-panel{position:absolute;left:96px;top:79px;width:344px;height:244px;background:rgba(20,20,22,.78);padding:18px 24px;color:#fff}
.hero-panel h1{font-family:"Lato",sans-serif;font-weight:400;font-size:19px;margin-bottom:12px}
.hero-panel p{font-family:"Open Sans",sans-serif;font-size:12.5px;line-height:1.55;text-align:justify}
.btn{display:inline-block;background:var(--brand);color:#fff;font-family:"Open Sans",sans-serif;font-weight:600;font-size:12.5px;text-decoration:none;text-align:center;border-radius:2px}
.hero-panel .btn{margin-top:16px;width:96px;height:30px;line-height:30px}
.hero-dots{position:absolute;left:563px;top:373px;display:flex;gap:8px}
.hero-dots span{width:7px;height:7px;border-radius:50%;background:#fff}

/* class descriptions */
.classes{top:499px;height:260px;background:var(--slate);color:#fff;text-align:center}
.section-title{font-family:"Lato",sans-serif;font-weight:400;font-size:22px;text-transform:uppercase}
.classes .section_title,.classes .section-title{margin-top:40px}
.caps-text{font-family:"Lato",sans-serif;font-size:11.4px;line-height:24px;letter-spacing:.35px;text-transform:uppercase}
.classes .caps-text{width:930px;margin:16px auto 0}
.classes .btn{margin-top:14px;width:96px;height:30px;line-height:30px}

/* gym description */
.gym{top:759px;height:338px}
.photo-circle{position:absolute;border-radius:50%}
.gym .photo-circle{left:144px;top:23px;width:280px;height:280px;background:radial-gradient(circle at 50% 40%,#3b6f4e,#1d3a7a 60%,#1a1f2c)}
.text-block{position:absolute}
.gym .text-block{left:497px;top:34px;width:588px}
.text-block h2{font-family:"Lato",sans-serif;font-weight:400;font-size:22px;color:#222;text-transform:uppercase}
.subtitle{font-size:10.8px;color:var(--brand);text-transform:uppercase;margin-top:2px}
.text-block .caps-text{color:var(--ink-soft);margin-top:16px;text-align:justify}
.text-block .btn{margin-top:10px;width:96px;height:30px;line-height:30px}

/* feature band */
.features{top:1097px;height:335px;background:linear-gradient(180deg,#4cb0cc,#2f9cbd)}
.feature{position:absolute;top:61px;width:275px;height:210px}
.feature-schedules{left:132px;background:rgba(20,22,25,.82);color:#fff;text-align:center;padding:18px 26px}
.feature-schedules h3{font-family:"Lato",sans-serif;font-weight:400;font-size:18px;text-transform:uppercase}
.feature-schedules p{font-family:"Open Sans",sans-serif;font-size:11.5px;line-height:1.55;margin-top:8px}
.feature-schedules .more{display:inline-block;margin-top:10px;font-size:11px;font-style:italic;font-weight:600}
.feature-photo{height:159px}
.feature-label{height:51px;line-height:51px;background:var(--brand);color:#fff;text-align:center;font-size:18px;text-transform:uppercase}
.feature-trainers{left:460px}
.feature-trainers .feature-photo{background:linear-gradient(135deg,#5a4a3c,#2c4d78 55%,#3a6a3e)}
.feature-philosophy{left:788px}
.feature-philosophy .feature-photo{background:linear-gradient(180deg,#e6e8ea,#9aa1a6 60%,#4a4d50)}

/* free trial */
.trial{top:1432px;height:348px}
.trial .text-block{left:98px;top:36px;width:637px}
.trial .photo-circle{left:795px;top:27px;width:280px;height:280px;background:radial-gradient(circle at 50% 45%,#cfd6da,#8f999f 55%,#4b5257)}

/* contact form */
.contact{top:1780px;height:405px;background:radial-gradient(ellipse at 50% 40%,#2a3138,var(--night) 70%);color:#fff}
.contact .section-title{text-align:center;margin-top:29px;font-size:21px}
.field-label{position:absolute;font-family:"Montserrat",sans-serif;font-weight:500;font-size:14.5px}
.field{position:absolute;background:#fff;border:0}
.submit{position:absolute;left:547px;top:337px;width:106px;height:42px;line-height:42px;font-size:14px}

/* footer */
.get-in-touch{top:2185px;height:186px;background:var(--brand);color:#fff;text-align:center}
.get-in-touch .section-title{margin-top:28px;font-size:23px}
.get-in-touch p{font-family:"Open Sans",sans-serif;font-size:12px;line-height:16px;width:520px;margin:12px auto 0}
.social{display:flex;justify-content:center;gap:10px;margin-top:14px}
.social span{width:24px;height:24px;border-radius:50%}
.footer-nav{display:flex;justify-content:center;gap:38px;margin-top:12px}
.footer-nav a{color:#fff;text-decoration:none;font-family:"Open Sans",sans-serif;font-size:12px}
.copyright{top:2371px;height:35px;background:var(--brand-deep);color:#fff;text-align:center;font-family:"Open Sans",sans-serif;font-size:10.5px;line-height:35px}
</style>
</head>
<body>
<div class="page">

  <header class="site-header">
    <div class="brand"><span class="brand-dot"></span><span class="brand-name">Summit</span></div>
    <nav class="main-nav">
      <a class="active" href="#">Home</a>
      <a href="#">Class descriptions</a>
      <a href="#">Gym description</a>
      <a href="#">Class schedules</a>
      <a href="#">Trainer profiles</a>
      <a href="#">Gym philosophy</a>
      <a href="#">Contact</a>
    </nav>
  </header>

  <section class="hero" role="img" aria-label="Gym interior with wooden wall, plant lettering, dumbbell racks, medicine balls and a barbell">
    <div class="hero-panel">
      <h1>WELCOME TO SUMMIT GYM</h1>
      <p>His at viris qualisque, id commune albucius dissentiet sit, ex sed nonumy delenit referrentur. Et vis commodo consequuntur. Cu volumus quaestio vis. Te quando urbanitas vix, oblique epicurei sed ad. Vitae iudico utinam ea mei. No eirmod graecis electram eum in the well.</p>
      <a class="btn" href="#">Read More</a>
    </div>
    <div class="hero-dots"><span></span><span></span><span></span><span></span><span></span></div>
  </section>

  <section class="classes">
    <h2 class="section-title">Class Descriptions</h2>
    <p class="caps-text">His at viris qualisque, id commune albucius dissentiet sit, ex sed nonumy delenit referrentur. Et vis commodo consequuntur. Cu volumus quaestio vis. Te quando urbanitas vix, oblique epicurei sed ad. Vitae iudico utinam ea mei. No eirmod graecis electram eum, ne pri tota semper electram.Diam maiestatis at eos, viderer repæÆudiandae intellegebat eu quo. Munere tractatos voluptatum an cum, dicam convenire ex vix. An nam summo novum, ullum cetero consetetur mea ad. Facer accusamus et vis, eu qui case option accommodare.</p>
    <a class="btn" href="#">Read More</a>
  </section>

  <section class="gym">
    <div class="photo-circle" role="img" aria-label="Athlete training on a blue calisthenics rig"></div>
    <div class="text-block">
      <h2>Gym Description</h2>
      <p class="subtitle">His at viris qualisque, id commune albucius dissentiet sit.</p>
      <p class="caps-text">His at viris qualisque, id commune albucius dissentiet sit, ex sed nonumy delenit referrentur. Et vis commodo consequuntur. Cu volumus quaestio vis. Te quando urbanitas vix, oblique epicurei sed ad. Vitae iudico utinam ea mei. No eirmod graecis electram eum, ne pri tota semper electram.Diam maiestatis at eos, viderer repæÆudiandae intellegebat eu quo. Munere tractatos voluptatum an cum, dicam convenire ex vix. An nam summo novum, ullum cetero consetetur mea ad. Facer accusamus et vis, eu qui case option accommodare. An quodsi verterem expetenda qui.</p>
      <a class="btn" href="#">Read More</a>
    </div>
  </section>

  <section class="features" role="img" aria-label="Blue-tinted view of the gym floor behind feature boxes">
    <div class="feature feature-schedules">
      <h3>Class Schedules</h3>
      <p>Erat fringilla aenean pulvinar condimentum velit urna, suspendisse vivam us duis gravida lorem. Ornare sit diam mori lobortis. Ut erat fusce tempor turpis.In ye dee himu 0c selendr Ornare sit diam.</p>
      <span class="more">Learn More ▸</span>
    </div>
    <div class="feature feature-trainers">
      <div class="feature-photo" role="img" aria-label="Trainer hanging from a pull-up bar"></div>
      <div class="feature-label">Trainer Profiles</div>
    </div>
    <div class="feature feature-philosophy">
      <div class="feature-photo" role="img" aria-label="Open training hall with calisthenics frames"></div>
      <div class="feature-label">Gym Philosophy</div>
    </div>
  </section>

  <section class="trial">
    <div class="text-block">
      <h2>Free First Trial Class</h2>
      <p class="subtitle">His at viris qualisque, id commune albucius dissentiet sit.</p>
      <p class="caps-text">His at viris qualisque, id commune albucius dissentiet sit, ex sed nonumy delenit referrentur. Et vis commodo consequuntur. Cu volumus quaestio vis. Te quando urbanitas vix, oblique epicurei sed ad. Vitae iudico utinam ea mei. No eirmod graecis electram eum, ne pri tota semper electram.Diam maiestatis at eos, viderer repæÆudiandae intellegebat eu quo. Munere tractatos voluptatum an cum, dicam convenire ex vix. An nam summo novum, ullum cetero consetetur mea ad. Facer accusamus et vis, eu qui case option accommodare. An quodsi verterem expetenda qui.In the rain ofte ware in the samy sed in the wall for in the day.</p>
      <a class="btn" href="#">Free Trail</a>
    </div>
    <div class="photo-circle" role="img" aria-label="Members training in a bright open gym hall"></div>
  </section>

  <section class="contact">
    <h2 class="section-title">Contacts</h2>
    <span class="field-label" style="left:130px;top:101px">Your Name*</span>
    <div class="field" style="left:128px;top:135px;width:438px;height:42px"></div>
    <span class="field-label" style="left:627px;top:101px">Your Company*</span>
    <div class="field" style="left:622px;top:135px;width:440px;height:42px"></div>
    <span class="field-label" style="left:130px;top:203px">How can we help you?</span>
    <div class="field" style="left:128px;top:238px;width:944px;height:79px"></div>
    <span class="btn submit">Submit</span>
  </section>

  <footer class="get-in-touch">
    <h2 class="section-title">Get In Touch</h2>
    <p>Lorem ipsum dolor sit amet, consectetur adipiscing elit. Maurissemper eu turpis sed, mollis vehicula neque. Ut in urna ante. Etiam sit amet arcu ante.</p>
    <div class="social">
      <span style="background:#3b5a98"></span>
      <span style="background:#42a8e0"></span>
      <span style="background:#d34836"></span>
      <span style="background:#c4302b"></span>
      <span style="background:#f2a93b"></span>
      <span style="background:#cb2027"></span>
    </div>
    <nav class="footer-nav">
      <a href="#">Home</a><a href="#">Class descriptions</a><a href="#">Gym description</a><a href="#">Class schedules</a><a href="#">Trainer profiles</a><a href="#">Gym philosophy</a><a href="#">Contact</a>
    </nav>
  </footer>

  <footer class="copyright">Copyright© 2015. All Rights Reserved.</footer>
</div>
</body>
</html>
```